Website for a Psychologist in Private Practice

I need a cool web design for my website: www.drkalvoric.com. I would like it to look professional. Keep all the current content and add: Space for video; radio spots (see Silver Cedar Tunes Logo below for those); Quick Inquiry; Friendora link; 5 star rating on Rivo; a map; reviews from former patients. I am open to suggestions.

Target Market(s)

Those seeking individual and marital counseling.

Industry/Entity Type

Mental Health

Number of Pages Required

1 page

Font styles to use
Sans Serif
Other font styles liked:
• I'm open but no hard to read script

Requirements
Must have
• All the content on my home page with link for video and radio spots. List services and degrees and expertices (pics not necessary).
Nice to have
• A video of me and radio conversations (logo of Silver Cedar Tunes radio attached).
Should not have
• Cartoons, comedy, etc.... I don't need pictures of services (marital, depression, etc...) Just list those.

```html
<!DOCTYPE html>
<html lang="en">
<head>
<meta charset="utf-8">
<title>Dr. Dana R. Kalvoric — Individual and Marital Counseling</title>
<link href="https://fonts.googleapis.com/css2?family=Lato:wght@300;400;700;900&family=Dancing+Script:wght@600;700&display=swap" rel="stylesheet">
<style>
:root{
  --gold:#c9a227;
  --gold-soft:#e3bf45;
  --blue:#2b7fc6;
  --blue-band:#3f93d4;
  --ink:#333;
  --muted:#777;
  --nav:#2f2f2f;
  --card:#e6e6e6;
  --footer:#2a2a2a;
  --footer-deep:#1c1c1c;
  --white:#fff;
}
*{box-sizing:border-box;margin:0;padding:0}
html,body{width:1200px;height:2664px;overflow:hidden}
body{font-family:'Lato',sans-serif;color:var(--ink);background:var(--white);font-size:15px}
.page{width:1200px;height:2664px;position:relative}

/* header */
.site-header{height:120px;display:flex;align-items:center;justify-content:space-between;padding:0 70px 0 60px}
.brand{font-family:'Lato',sans-serif;font-weight:700;font-size:34px;color:var(--gold);letter-spacing:.5px}
.contact-strip{display:flex;gap:46px;font-size:15px;color:#555}
.contact-strip span{display:flex;align-items:center;gap:10px}
.contact-strip svg{width:28px;height:28px}

/* nav */
.main-nav{height:60px;background:var(--nav);display:flex;padding-left:60px}
.main-nav a{color:var(--white);text-decoration:none;font-weight:700;font-size:15px;letter-spacing:.5px;padding:0 40px;display:flex;align-items:center}
.main-nav a.active{background:var(--blue)}

/* hero */
.hero{height:480px;position:relative;background:linear-gradient(100deg,#cfd6dc 0%,#b9c3cc 45%,#e7dccd 70%,#d9d9d6 100%)}
.hero-caption{position:absolute;left:0;right:0;bottom:0;height:64px;background:rgba(20,20,20,.72);color:var(--white);font-size:30px;font-weight:400;display:flex;align-items:center;justify-content:center}
.hero-arrow{position:absolute;top:200px;width:28px;height:40px;background:rgba(0,0,0,.7);display:flex;align-items:center;justify-content:center}
.hero-arrow.prev{left:0}.hero-arrow.next{right:0}

/* about */
.about{height:450px;position:relative;padding:70px 60px 0}
.script{font-family:'Dancing Script',cursive;color:var(--gold);font-weight:700}
.about h2{font-size:36px;font-weight:700;color:#222;margin-bottom:22px}
.about h2 .script{font-size:40px}
.about-text{width:740px;font-size:13.5px;line-height:1.65;color:#555}
.about-text b{color:var(--blue)}
.values{display:flex;gap:60px;margin-top:34px}
.value{display:flex;gap:16px;width:290px}
.value-icon{width:60px;height:60px;border:2px solid var(--gold);border-radius:50%;flex:none;display:flex;align-items:center;justify-content:center}
.value h3{font-size:20px;color:var(--blue);font-weight:400;margin-bottom:6px}
.value p{font-size:13px;color:#666;line-height:1.5}
.inquiry{position:absolute;right:60px;top:70px;width:290px;height:340px;background:#f1f1f1;border:1px solid #ddd}
.inquiry h4{background:var(--blue);color:var(--white);font-size:17px;padding:14px 18px;font-weight:700;letter-spacing:.5px}
.inquiry form{padding:14px 18px}
.field{height:32px;background:var(--white);border:1px solid #d7d7d7;margin-bottom:10px;font-size:12px;color:#999;padding:8px 10px;display:flex;justify-content:space-between}
.field.msg{height:60px}
.submit{display:inline-block;background:var(--blue);color:var(--white);font-size:13px;font-weight:700;padding:10px 18px;margin-top:2px}

/* sessions */
.sessions{height:360px;display:flex;margin-top:20px}
.sessions-list{width:600px;background:var(--gold-soft);color:var(--white);padding:34px 70px}
.sessions-list .sess-icon{display:block;margin:0 auto 6px;width:50px}
.sessions-list h2{font-size:36px;font-weight:700;margin-bottom:16px}
.sessions-list ul{list-style:none;display:grid;grid-template-columns:1fr 1fr;gap:5px 30px;font-size:14px;font-weight:700}
.sessions-list li::before{content:"■";font-size:8px;margin-right:8px;vertical-align:2px}
.btn-outline{display:inline-block;margin-top:24px;border:2px solid var(--white);padding:9px 26px;font-weight:700;font-size:14px}
.video{width:600px;background:var(--blue-band);color:var(--white);display:flex;flex-direction:column;align-items:center;justify-content:center;gap:24px}
.video p{font-size:18px}
.video strong{font-size:18px;letter-spacing:.5px}

/* expertise */
.expertise{height:610px;padding-top:50px;text-align:center}
.section-title{font-size:42px;color:#222;font-weight:700;margin-bottom:30px}
.section-title .script{font-size:44px}
.cards{display:grid;grid-template-columns:repeat(4,250px);gap:12px;justify-content:center}
.card{background:var(--card);height:220px;position:relative;padding:30px 22px 0;overflow:hidden}
.card svg.icon{width:52px;height:52px}
.card h3{font-size:14px;font-weight:700;margin:12px 0 10px;letter-spacing:.5px;color:#333}
.card p{font-size:13px;color:#666;line-height:1.45}
.card::after{content:"";position:absolute;right:0;bottom:0;border-style:solid;border-width:0 0 34px 34px;border-color:transparent transparent var(--gold-soft) transparent}

/* radio */
.radio{height:290px;text-align:center;position:relative;padding-top:44px}
.radio .section-title{margin-bottom:22px}
.quote{width:900px;margin:0 auto;font-size:14px;line-height:1.6;color:#666}
.quote::before{content:"“";font-size:30px;color:var(--gold);margin-right:8px;vertical-align:-6px}
.reviewer{margin-top:16px;font-size:17px;color:var(--gold)}
.radio .arrow{position:absolute;top:150px;font-size:32px;color:#bbb}
.radio .arrow.l{left:75px}.radio .arrow.r{right:75px}

/* footer */
.site-footer{height:254px;position:relative;background:var(--footer)}
.map{position:absolute;inset:0;background:linear-gradient(135deg,#2e2e2e,#3a3a3a 50%,#2a2a2a)}
.footer-inner{position:relative;padding-top:26px;color:var(--white);text-align:center}
.donate{display:flex;align-items:center;justify-content:center;gap:20px;font-size:16px;font-weight:700}
.badge{width:96px;height:46px;background:#f3f3f3;border-radius:3px}
.contact-row{display:flex;justify-content:center;gap:90px;margin-top:50px;font-size:14px}
.contact-row span{display:flex;align-items:center;gap:10px}
.copyright{position:absolute;left:0;right:0;bottom:0;height:40px;background:var(--footer-deep);color:#aaa;font-size:12px;display:flex;align-items:center;justify-content:center}
</style>
</head>
<body>
<div class="page">

<header class="site-header">
  <div class="brand">Dr. Dana R. Kalvoric</div>
  <div class="contact-strip">
    <span><svg viewBox="0 0 28 28"><circle cx="14" cy="14" r="13" fill="#eee"/><rect x="7" y="9" width="14" height="10" fill="none" stroke="#c9a227" stroke-width="1.6"/><path d="M7 9l7 6 7-6" fill="none" stroke="#c9a227" stroke-width="1.6"/></svg>Email Us: info@drkalvoric.com</span>
    <span><svg viewBox="0 0 28 28"><circle cx="14" cy="14" r="13" fill="#eee"/><path d="M10 8l3 3-2 2c1 2 2 3 4 4l2-2 3 3-2 2c-5-1-9-5-10-10z" fill="#c9a227"/></svg>Call Us: (555) 014-2287</span>
  </div>
</header>

<nav class="main-nav">
  <a class="active">HOME</a><a>BIO</a><a>MY EXPERTISE</a><a>SESSIONS</a><a>RESOURCES</a><a>CONTACT ME</a>
</nav>

<section class="hero" role="img" aria-label="Photo of a counselor comforting a distressed woman in a bright office">
  <div class="hero-arrow prev"><svg width="10" height="14"><path d="M8 1L2 7l6 6" stroke="#fff" stroke-width="2" fill="none"/></svg></div>
  <div class="hero-arrow next"><svg width="10" height="14"><path d="M2 1l6 6-6 6" stroke="#fff" stroke-width="2" fill="none"/></svg></div>
  <div class="hero-caption">I Provide individual and marital counseling</div>
</section>

<section class="about">
  <h2><span class="script">About</span> <span class="script">Dr. Dana R. Kalvoric</span></h2>
  <p class="about-text">While I acknowledge the importance of my education, I also appreciate the role my experience has played in allowing me to relate so well to others. Allow me to share those I feel are most relevant with you. I survived an abusive childhood from my mother and sister, unfortunately still not ... <b>Read More</b></p>
  <div class="values">
    <div class="value">
      <div class="value-icon"><svg width="30" height="30" viewBox="0 0 30 30"><circle cx="15" cy="12" r="8" fill="none" stroke="#2b7fc6" stroke-width="2"/><path d="M11 22h8M12 26h6" stroke="#2b7fc6" stroke-width="2"/></svg></div>
      <div><h3>My Philosophy</h3><p>Lorem ipsum dolor sit amet, conse ctetuer adipiscing elit.</p></div>
    </div>
    <div class="value">
      <div class="value-icon"><svg width="30" height="30" viewBox="0 0 30 30"><circle cx="15" cy="15" r="11" fill="none" stroke="#2b7fc6" stroke-width="2"/><circle cx="15" cy="15" r="5" fill="none" stroke="#2b7fc6" stroke-width="2"/><circle cx="15" cy="15" r="1.5" fill="#2b7fc6"/></svg></div>
      <div><h3>My Mission</h3><p>Lorem ipsum dolor sit amet, conse ctetuer adipiscing elit.</p></div>
    </div>
  </div>
  <aside class="inquiry">
    <h4>QUICK INQUIRY</h4>
    <form>
      <div class="field">Full Name</div>
      <div class="field">Phone Number</div>
      <div class="field">Email <span>▾</span></div>
      <div class="field msg">Message</div>
      <span class="submit">SUBMIT</span>
    </form>
  </aside>
</section>

<section class="sessions">
  <div class="sessions-list">
    <svg class="sess-icon" viewBox="0 0 50 40"><circle cx="25" cy="10" r="8" fill="#fff"/><path d="M10 38c0-10 7-16 15-16s15 6 15 16z" fill="#fff"/></svg>
    <h2>Type of Sessions I Provide</h2>
    <ul>
      <li>Individual Sessions</li><li>Divorce Mediation</li>
      <li>Marriage Sessions</li><li>Custody Evaluation Sessions</li>
      <li>Family Sessions</li><li>Evening Sessions</li>
      <li>Phone Sessions</li><li>Weekend / Holiday Sessions</li>
    </ul>
    <span class="btn-outline">Get Started</span>
  </div>
  <div class="video" role="img" aria-label="Introductory video of the psychologist">
    <p>Lorem ipsum dolor sit amet, consectetu</p>
    <svg width="46" height="34" viewBox="0 0 46 34"><rect width="46" height="34" rx="8" fill="#fff"/><path d="M18 10l12 7-12 7z" fill="#3f93d4"/></svg>
    <strong>WATCH VIDEO</strong>
  </div>
</section>

<section class="expertise">
  <h2 class="section-title"><span class="script">My</span> <span class="script">Expertise</span></h2>
  <div class="cards">
    <div class="card"><svg class="icon" viewBox="0 0 52 52"><path d="M26 44L8 26a10 10 0 0 1 18-12 10 10 0 0 1 18 12z" fill="#333"/></svg><h3>DATING</h3><p>Lorem ipsum dolor sit amet, consectetuer adipiscing elit, sed diam nonummy nibh</p></div>
    <div class="card"><svg class="icon" viewBox="0 0 52 52"><circle cx="20" cy="28" r="11" fill="none" stroke="#333" stroke-width="4"/><circle cx="32" cy="28" r="11" fill="none" stroke="#333" stroke-width="4"/></svg><h3>MARRIAGE</h3><p>Lorem ipsum dolor sit amet, consectetuer adipiscing elit, sed diam nonummy nibh</p></div>
    <div class="card"><svg class="icon" viewBox="0 0 52 52"><rect x="14" y="8" width="30" height="22" fill="#333"/><circle cx="12" cy="30" r="5" fill="#333"/><path d="M4 48c0-8 4-12 8-12s8 4 8 12z" fill="#333"/></svg><h3>PARENTING &amp; PROFESSIONAL</h3><p>Lorem ipsum dolor sit amet, consectetuer adipiscing elit, sed diam nonummy nibh</p></div>
    <div class="card"><svg class="icon" viewBox="0 0 52 52"><circle cx="18" cy="16" r="7" fill="#333"/><circle cx="34" cy="16" r="7" fill="#333"/><path d="M6 44c0-12 6-18 12-18s12 6 12 18zM22 44c0-12 6-18 12-18s12 6 12 18z" fill="#333"/></svg><h3>RELATIONSHIPS</h3><p>Lorem ipsum dolor sit amet, consectetuer adipiscing elit, sed diam nonummy nibh</p></div>
    <div class="card"><svg class="icon" viewBox="0 0 52 52"><circle cx="26" cy="26" r="18" fill="none" stroke="#333" stroke-width="4"/><path d="M18 34q8-8 16 0" fill="none" stroke="#333" stroke-width="3"/><circle cx="20" cy="22" r="2.5" fill="#333"/><circle cx="32" cy="22" r="2.5" fill="#333"/></svg><h3>DEPRESSION &amp; ANXIETY ISSUES</h3><p>Lorem ipsum dolor sit amet, consectetuer adipiscing elit, sed diam nonummy nibh</p></div>
    <div class="card"><svg class="icon" viewBox="0 0 52 52"><circle cx="18" cy="26" r="12" fill="#333"/><circle cx="34" cy="26" r="12" fill="none" stroke="#333" stroke-width="3"/></svg><h3>PERSONALITY DISORDERS</h3><p>Lorem ipsum dolor sit amet, consectetuer adipiscing elit, sed diam nonummy nibh</p></div>
    <div class="card"><svg class="icon" viewBox="0 0 52 52"><path d="M26 8v36M10 18h32M10 18l-6 14h12zM42 18l-6 14h12z" fill="none" stroke="#333" stroke-width="3"/><rect x="18" y="42" width="16" height="4" fill="#333"/></svg><h3>DIVORCE MEDIATION</h3><p>Lorem ipsum dolor sit amet, consectetuer adipiscing elit, sed diam nonummy nibh</p></div>
    <div class="card"><svg class="icon" viewBox="0 0 52 52"><circle cx="26" cy="26" r="6" fill="#333"/><path d="M26 6v10M26 36v10M6 26h10M36 26h10M12 12l7 7M33 33l7 7M40 12l-7 7M19 33l-7 7" stroke="#333" stroke-width="4"/></svg><h3>LIFE MANAGEMENT</h3><p>Lorem ipsum dolor sit amet, consectetuer adipiscing elit, sed diam nonummy nibh</p></div>
  </div>
</section>

<section class="radio">
  <h2 class="section-title"><span class="script">Radio</span> <span class="script">Conversations</span></h2>
  <p class="quote">Lorem ipsum dolor sit amet, consectetuer adipiscing elit, sed diam nonummy tincidunt ut laoreet dolore magna aliquam erat volutpat. Ut wisi enim ad minim veniam, quis nostrud exerci tation ullamcorper suscipit lobortis nisl ut aliquip ex ea commodo consequat. Duis autem vel eum iriure.</p>
  <p class="reviewer">Sam Whitley</p>
  <span class="arrow l">‹</span><span class="arrow r">›</span>
</section>

<footer class="site-footer">
  <div class="map" role="img" aria-label="Dark street map showing the office location"></div>
  <div class="footer-inner">
    <div class="donate">A portion of all revenue is donated to <span class="badge"></span><span class="badge"></span></div>
    <div class="contact-row">
      <span><svg width="16" height="22" viewBox="0 0 16 22"><path d="M8 0a8 8 0 0 1 8 8c0 6-8 14-8 14S0 14 0 8a8 8 0 0 1 8-8z" fill="#c9a227"/><circle cx="8" cy="8" r="3" fill="#2a2a2a"/></svg>418 Alder Lane, Suite 210 Harbor Point, CA 90000</span>
      <span><svg width="18" height="18" viewBox="0 0 18 18"><path d="M3 1l4 4-2 2c1 3 3 5 6 6l2-2 4 4-3 3C7 17 1 11 0 4z" fill="#c9a227"/></svg>(555) 014-2287</span>
      <span><svg width="20" height="14" viewBox="0 0 20 14"><rect x="1" y="1" width="18" height="12" fill="none" stroke="#c9a227" stroke-width="1.6"/><path d="M1 1l9 7 9-7" fill="none" stroke="#c9a227" stroke-width="1.6"/></svg>info@drkalvoric.com</span>
    </div>
  </div>
  <div class="copyright">Copyright © 2015 Dr. Dana R. Kalvoric. All Right Reserved.</div>
</footer>

</div>
</body>
</html>
```